Business Card (double-sided) and Stationary Design for dental office

1) Business Card Design: We need a business card design for a dental specialty office.
Texts should contain:
The name of our office "Brindle Oaks Orthodontics"
Tagline: "Specialist in Orthodontic and Maxillofacial Orthopedics"
Tag line: "Creating "Tolvering" smiles for Children and Adults"
Doctor name: "Doctor Name"
Office Address:
"123 Street Name
City, State Zip code"
Office email address: office@brindleoaksortho.com
Website: www.brindleoaksortho.com

We will provide the full office address once the design is selected
Theme: beach, paradise, coastal, wave
We would like to have some creativity in design. Some acceptable ideas: front page: logo and office name. Back page: more detail information, and map to office in form of an island. Please see sample from our other location, but you DON'T HAVE TO USE OR COPY THE SAME CONCEPT.

IF POSSIBLE, PLEASE SUBMIT AT LEAST TWO CONCEPTS: ONE WITH THE BACK LOOKING SIMILAR TO WHAT IS IN THE SAMPLE, AND ONE DIFFERENT.

Color: designer to choose. We have different shade of blues and sand color in our office. Please see logo.

2) Please also design a matching set of stationary that compliment the business card and our logo.

Target Market(s)

Dental

Contact Information for Business Card

See descriptions

Font styles to use
Other font styles liked:
• Matching texts in logo

Colors
0054AA
0677BA
7BADD7
CADEEF
E8F1F8
0094D4
00A9DD
6FCCEA
C7EBF8
E9F6FB
00AB8E
00BBA5
67D7C9
C6EFE9
E9F9F6

Requirements
Must have
• Double-sided
Nice to have
• Beach coastal theme
Should not have
• Any shape or drawing of of tooth or teeth. We don’t need these. You don't necessarily have to just cut and paste the logo art and text as a whole, you have the liberty to rearrange the text.

```html
<!DOCTYPE html>
<html lang="en">
<head>
<meta charset="utf-8">
<title>Brindle Oaks Orthodontics – Stationery Set</title>
<link rel="stylesheet" href="https://fonts.googleapis.com/css2?family=Raleway:wght@300;400;600;700&family=Ubuntu:wght@500&display=swap">
<style>
:root{
  --backdrop:#959293;
  --paper:#f3f2f2;
  --teal-deep:#3a8aa3;
  --teal-mint:#7ecdbf;
  --brand:#2f8fa6;
  --brand-soft:#5fb9c9;
  --ink:#4a4a4a;
  --ink-soft:#6d6d6d;
  --faint:rgba(58,138,163,.12);
  --sky-top:#a9d9f1;
  --sky-bottom:#eef8fd;
  --sea:#1ea4dc;
  --sand:#e9c784;
  --palm:#5c9a4a;
}
*{box-sizing:border-box;margin:0;padding:0}
html,body{width:1200px;height:826px;overflow:hidden}
body{background:var(--backdrop);font-family:"Raleway",sans-serif;color:var(--ink);position:relative}
.piece{position:absolute;background:var(--paper);overflow:hidden}

/* shared brand lockup */
.brand-mark{position:absolute;border-radius:50%;background:var(--brand);border:2px solid #fff}
.brand-name{position:absolute;font-family:"Raleway",sans-serif;font-weight:700;color:var(--brand);white-space:nowrap;text-align:center;transform:translateX(-50%)}
.brand-tag{position:absolute;font-family:"Raleway",sans-serif;font-weight:600;color:var(--brand-soft);letter-spacing:.08em;white-space:nowrap;text-align:center;transform:translateX(-50%)}
.band{position:absolute;left:0;right:0;background:linear-gradient(90deg,var(--teal-deep) 0 50%,var(--teal-mint) 50% 100%)}
.ghost-circle{position:absolute;border-radius:50%;background:var(--faint)}

/* letterhead */
.letterhead{left:60px;top:112px;width:462px;height:645px}
.letterhead .band{top:35px;height:45px}
.letter-greeting{position:absolute;left:41px;top:183px;font-size:11.5px;font-weight:400}
.letter-body{position:absolute;left:41px;top:214px;width:381px;font-size:7px;line-height:9.8px;font-weight:400;color:var(--ink-soft);text-align:justify}
.letter-body p{margin-bottom:9.8px}
.letter-closing{position:absolute;left:41px;top:424px;font-size:6.8px;color:var(--ink-soft)}
.signature-area{position:absolute;left:41px;top:448px;width:56px;height:20px;background:rgba(40,40,40,.08)}
.contact-list{position:absolute;list-style:none;font-weight:400;color:var(--ink-soft)}
.contact-list li{display:flex;align-items:center;gap:5px}
.contact-list svg{flex:none}
.letterhead .contact-list{left:43px;top:580px;font-size:9px;line-height:11.5px}
.address-block{position:absolute;text-align:right;color:var(--ink-soft);font-weight:400}
.letterhead .address-block{right:40px;top:582px;font-size:9px;line-height:11px}

/* business card */
.business-card{left:550px;top:120px;width:288px;height:164px}
.business-card .band{top:29px;height:26px;background:linear-gradient(90deg,var(--teal-deep) 0 74%,var(--teal-mint) 74% 100%)}
.holder-name{position:absolute;left:25px;top:36px;font-family:"Ubuntu",sans-serif;font-weight:500;font-size:11.5px;color:#fff;letter-spacing:.03em}
.business-card .contact-list{left:26px;top:117px;font-size:6.6px;line-height:8.2px}
.business-card .address-block{right:28px;top:117px;font-size:6.6px;line-height:8.2px}

/* appointment card */
.appointment-card{left:862px;top:120px;width:288px;height:165px;background:linear-gradient(180deg,var(--sky-top),var(--sky-bottom) 70%)}
.appointment-title{position:absolute;left:15px;top:16px;font-size:6.8px;font-weight:700;color:#1f6f8f;letter-spacing:.01em}
.appointment-field{position:absolute;left:15px;font-size:6.4px;color:#3d5a66;display:flex;align-items:flex-end;gap:2px}
.appointment-field span.rule{display:block;border-bottom:1px dotted #6f8f9c;height:6px}
.sea-band{position:absolute;left:0;right:0;bottom:0;height:50px;background:var(--sea)}
.island-scene{position:absolute;right:0;top:26px;width:118px;height:139px;background:linear-gradient(180deg,var(--palm) 0%,var(--sand) 55%,var(--sea) 100%)}
.appointment-tagline{position:absolute;left:10px;top:136px;font-size:6.2px;font-weight:700;font-style:italic;color:#fff;line-height:8px}

/* envelope back */
.envelope-back{left:602px;top:337px;width:530px;height:240px}
.envelope-back .flap{position:absolute;left:0;top:0}

/* envelope front */
.envelope-front{left:565px;top:511px;width:530px;height:241px}
.envelope-front .band{top:26px;height:46px;background:linear-gradient(90deg,var(--teal-deep) 0 19%,var(--teal-mint) 19% 100%)}
.envelope-front .address-block{left:25px;top:107px;text-align:left;font-size:9.2px;line-height:11px;color:#3b3b3b}
</style>
</head>
<body>

<section class="piece letterhead" aria-label="Letterhead">
  <div class="band"></div>
  <div class="ghost-circle" style="left:125px;top:228px;width:212px;height:212px"></div>
  <div class="brand-mark" style="left:205px;top:33px;width:50px;height:50px"></div>
  <div class="brand-name" style="left:231px;top:84px;font-size:15px">Brindle Oaks</div>
  <div class="brand-tag" style="left:231px;top:103px;font-size:5.6px">Pediatric Dentistry &amp; Orthodontics</div>

  <p class="letter-greeting">Dear Mr. Harrow,</p>
  <div class="letter-body">
    <p>Thank you for choosing our practice for your family's orthodontic care. We are pleased to confirm that your treatment plan is now ready, and our whole team looks forward to welcoming you back very soon. Please review the enclosed notes before your next visit so that we can answer any questions together, and feel free to bring a list of anything you would like to discuss with the doctor.</p>
    <p>Regular adjustments keep progress on schedule, so we kindly ask that appointments be kept or rescheduled at least one day in advance. Our front desk can help arrange times that suit school and work, and reminders will be sent by email a few days before each visit. Evening and weekend slots are limited, so we suggest booking them early.</p>
    <p>Between visits, brush after every meal and avoid hard or sticky foods that may loosen brackets or bend wires. If a wire or band feels uncomfortable, call our office and we will find a time to see you quickly. Small issues are easy to fix when they are reported early, and most can be handled in a short visit. Wax from your starter kit can ease any rubbing until then, and a soft diet for a day or two helps after each adjustment.</p>
    <p>We are grateful for your trust and look forward to building a bright, healthy smile with you. Should you have any questions about billing, insurance or your schedule, our team is always happy to help by phone or email.</p>
  </div>
  <p class="letter-closing">Sincerely,</p>
  <div class="signature-area" role="img" aria-label="Handwritten signature"></div>

  <ul class="contact-list">
    <li><svg width="7" height="7" viewBox="0 0 10 10"><path d="M2 1l2 2-1 1.5c.7 1.3 1.8 2.4 3 3L7.5 6l2 2-1.5 1.5C4 9 1 6 .5 1.5z" fill="var(--brand)"/></svg>555-214-0873</li>
    <li><svg width="7" height="7" viewBox="0 0 10 10"><rect x="0.5" y="2" width="9" height="6" fill="var(--brand)"/><path d="M.5 2l4.5 3.5L9.5 2" stroke="#fff" fill="none"/></svg>office@brindleoaksortho.com</li>
    <li><svg width="7" height="7" viewBox="0 0 10 10"><circle cx="5" cy="5" r="4.5" fill="var(--brand)"/><path d="M.5 5h9M5 .5c-2 3-2 6 0 9M5 .5c2 3 2 6 0 9" stroke="#fff" stroke-width=".7" fill="none"/></svg>www.brindleoaksortho.com</li>
  </ul>
  <div class="address-block">Brindle Oaks Dentistry<br>123 Street Name<br>City, State Zip code</div>
</section>

<section class="piece business-card" aria-label="Business card">
  <div class="ghost-circle" style="left:-8px;top:78px;width:96px;height:96px"></div>
  <div class="band"></div>
  <p class="holder-name">Daniel Harrow</p>
  <div class="brand-mark" style="left:190px;top:20px;width:44px;height:44px"></div>
  <div class="brand-name" style="left:212px;top:67px;font-size:12px">Brindle Oaks</div>
  <div class="brand-tag" style="left:212px;top:82px;font-size:4.4px">Pediatric Dentistry &amp; Orthodontics</div>
  <ul class="contact-list">
    <li><svg width="5" height="5" viewBox="0 0 10 10"><path d="M2 1l2 2-1 1.5c.7 1.3 1.8 2.4 3 3L7.5 6l2 2-1.5 1.5C4 9 1 6 .5 1.5z" fill="var(--brand)"/></svg>555-214-0873</li>
    <li><svg width="5" height="5" viewBox="0 0 10 10"><rect x="0.5" y="2" width="9" height="6" fill="var(--brand)"/></svg>office@brindleoaksortho.com</li>
    <li><svg width="5" height="5" viewBox="0 0 10 10"><circle cx="5" cy="5" r="4.5" fill="var(--brand)"/></svg>brindleoaksortho.com</li>
  </ul>
  <div class="address-block">Brindle Oaks Dentistry<br>123 Street Name<br>City, State Zip code</div>
</section>

<section class="piece appointment-card" aria-label="Appointment card">
  <p class="appointment-title">SEE YOU AT YOUR NEXT APPOINTMENT!</p>
  <p class="appointment-field" style="top:40px">For<span class="rule" style="width:138px"></span></p>
  <p class="appointment-field" style="top:62px">Date<span class="rule" style="width:134px"></span></p>
  <p class="appointment-field" style="top:84px">Time<span class="rule" style="width:134px"></span></p>
  <div class="sea-band"></div>
  <div class="island-scene" role="img" aria-label="Illustration of a sandy island with palm trees in the sea, with a small map to the office"></div>
  <p class="appointment-tagline">Specialist in Orthodontic<br>&amp; Maxillofacial Orthopedics</p>
</section>

<section class="piece envelope-back" aria-label="Envelope back">
  <svg class="flap" width="530" height="78" viewBox="0 0 530 78" aria-hidden="true">
    <path d="M0 0H530C522 30 520 60 498 72Q490 76 470 76H62Q40 76 32 70C10 58 8 30 0 0Z" fill="var(--teal-deep)"/>
  </svg>
  <div class="brand-mark" style="left:231px;top:16px;width:44px;height:44px;background:transparent"></div>
</section>

<section class="piece envelope-front" aria-label="Envelope front">
  <div class="ghost-circle" style="left:312px;top:49px;width:184px;height:184px"></div>
  <div class="band"></div>
  <div class="brand-mark" style="left:63px;top:24px;width:50px;height:50px"></div>
  <div class="brand-name" style="left:150px;top:76px;font-size:15px">Brindle Oaks</div>
  <div class="brand-tag" style="left:150px;top:94px;font-size:5.6px">Pediatric Dentistry &amp; Orthodontics</div>
  <div class="address-block">Brindle Oaks Dentistry<br>123 Street Name, City, State Zip code</div>
</section>

</body>
</html>
```